SUPPLEMENT BOTTLE LABEL: TOLVERIN

We need a NEW FRESH look to her labels. Something contemporary, clean and professional. The colors need to remain the same but everything else can change, even the logo.

THE CURRENT LABEL IS ATTACHED IN PDF FORMAT

Target Market(s)

WOMEN BETWEEN 35-60

Requirements
Must have
• SAME COLORS
• FRESH
• CLEAN

```html
<!DOCTYPE html>
<html lang="en">
<head>
<meta charset="UTF-8">
<title>Clearwell Renew – Cleanse Chocolate Label</title>
<link rel="stylesheet" href="https://fonts.googleapis.com/css2?family=Bungee&family=Sniglet:wght@400;800&display=swap">
<style>
  :root {
    --page-bg: #ecebef;
    --label-top: #e4f2f6;
    --label-mid: #9fd6e3;
    --label-low: #45b3cb;
    --label-base: #2f9fbc;
    --brand-teal: #2b9fb2;
    --ink: #14202a;
    --pill: #2a8ea6;
    --white: #ffffff;
  }
  * { margin: 0; padding: 0; box-sizing: border-box; }
  html, body { width: 1200px; height: 1200px; overflow: hidden; }
  body {
    background: var(--page-bg);
    font-family: "Sniglet", "Trebuchet MS", sans-serif;
    color: var(--ink);
    position: relative;
  }
  .label {
    position: absolute;
    left: 200px;
    top: 120px;
    width: 800px;
    height: 960px;
    background: linear-gradient(180deg, var(--label-top) 0%, #d3ebf2 22%, var(--label-mid) 45%, var(--label-low) 72%, var(--label-base) 100%);
    text-align: center;
    overflow: hidden;
  }
  .brand-name {
    position: absolute;
    top: 130px;
    left: 0;
    width: 100%;
    font-weight: 800;
    font-size: 76px;
    line-height: 1;
    color: var(--brand-teal);
  }
  .flavor-box {
    position: absolute;
    top: 300px;
    left: 155px;
    width: 500px;
    height: 215px;
    border: 4px solid var(--ink);
    border-radius: 22px;
    background: rgba(255,255,255,0.18);
  }
  .flavor-title {
    position: absolute;
    top: 318px;
    left: 0;
    width: 100%;
    font-family: "Bungee", "Arial Black", sans-serif;
    font-size: 70px;
    line-height: 92px;
    color: var(--white);
    -webkit-text-stroke: 3px var(--ink);
    paint-order: stroke fill;
    letter-spacing: 1px;
  }
  .flavor-note {
    position: absolute;
    top: 508px;
    left: 135px;
    width: 535px;
    height: 58px;
    border-radius: 29px;
    background: var(--pill);
    font-size: 33px;
    line-height: 58px;
    color: var(--ink);
  }
  .supplement-facts {
    position: absolute;
    top: 604px;
    left: 0;
    width: 100%;
    font-size: 27px;
    line-height: 42px;
  }
  .net-weight {
    position: absolute;
    top: 822px;
    left: 0;
    width: 100%;
    display: flex;
    justify-content: center;
    align-items: center;
    gap: 10px;
    font-size: 27px;
  }
  .net-weight .rule {
    width: 62px;
    height: 3px;
    background: var(--ink);
  }
</style>
</head>
<body>
  <section class="label">
    <div class="brand-name">Clearwell Renew</div>
    <div class="flavor-box"></div>
    <h1 class="flavor-title">CLEANSE<br>CHOCOLATE</h1>
    <div class="flavor-note">with other natural flavors</div>
    <p class="supplement-facts">
      Collagen, Multivitamin, Mineral &amp;<br>
      Herbal Dietary Supplement Powder<br>
      Notice: Use this product as a food supplement only.<br>
      Do not use for weight reduction.
    </p>
    <div class="net-weight"><span class="rule"></span>NET WT. 1.21 LBS (551.2 G)<span class="rule"></span></div>
  </section>
</body>
</html>
```